female esthetician looking for an impact business card

I an an expert in skin care industry with high experience in NYC.I want my business card to look professional , an impact at first look. I do want a combination between white and gold . I believe the font will be great if is gold.. The Fonts are also important. MIRABELA COSTINA (SKIN CARE BOUTIQUE)

THIS SHOULD BE THE BUSINESS NAME, and should be placed on th eback of the card.
IN front m, the name MIRABELA COSTINA - ESTHETCIAN

BY APPOINTMENTS ONLY: 518.240.7136

Target Market(s)

HIGH END CLIENTELE

Contact Information for Business Card

iT WILL BE on a luxury paper. I neeed the wow feeling

Requirements
Should not have
• pictures

```html
<!DOCTYPE html>
<html lang="en">
<head>
<meta charset="utf-8">
<title>Mirabela Costina – Skin Care Boutique Business Card</title>
<link rel="stylesheet" href="https://fonts.googleapis.com/css2?family=Questrial&display=swap">
<style>
  :root {
    --backdrop: #e8e3db;
    --card-white: #fbfbfa;
    --card-edge: #ddd8cf;
    --gold: #a7793a;
    --gold-deep: #8f6429;
  }
  * { margin: 0; padding: 0; box-sizing: border-box; }
  html, body {
    width: 800px;
    height: 1200px;
    overflow: hidden;
    background: var(--backdrop);
  }
  .canvas {
    position: relative;
    width: 800px;
    height: 1200px;
    font-family: "Questrial", "Helvetica Neue", Arial, sans-serif;
    color: var(--gold);
  }
  .card {
    position: absolute;
    left: 83px;
    width: 626px;
    height: 357px;
    background: var(--card-white);
    border: 1px solid var(--card-edge);
    border-radius: 20px;
  }
  .card--front { top: 102px; }
  .card--back  { top: 642px; }

  .brand {
    position: absolute;
    left: 0;
    right: 0;
    top: 148px;
    text-align: center;
  }
  .brand__name {
    display: inline-block;
    font-size: 36px;
    letter-spacing: 1px;
    color: var(--gold);
    line-height: 1;
    padding: 0 2px 5px;
    border-bottom: 1.5px solid var(--gold);
  }
  .brand__tagline {
    margin-top: 6px;
    font-size: 13px;
    letter-spacing: 3px;
    color: var(--gold);
  }

  .booking {
    position: absolute;
    left: 0;
    right: 0;
    top: 140px;
    text-align: center;
  }
  .booking__note {
    font-size: 24px;
    letter-spacing: 4.5px;
    color: var(--gold-deep);
    -webkit-text-stroke: 0.5px var(--gold-deep);
  }
  .booking__phone {
    margin-top: 10px;
    font-size: 24px;
    letter-spacing: 0.5px;
    color: var(--gold);
  }
</style>
</head>
<body>
  <main class="canvas">
    <section class="card card--front" aria-label="Card front">
      <div class="brand">
        <div class="brand__name">Mirabela Costina</div>
        <div class="brand__tagline">SKIN CARE BOUTIQUE</div>
      </div>
    </section>

    <section class="card card--back" aria-label="Card back">
      <div class="booking">
        <p class="booking__note">BY APPOINTMENTS ONLY</p>
        <p class="booking__phone">518.240.7136</p>
      </div>
    </section>
  </main>
</body>
</html>
```